Hop Bright Meadow Business Website Branding

Looking for a wordpress template design with CSS and HTML encoding. Current website can be seen at hopbrightmeadow.example.

WE ARE CURRENTLY IN PROCESS GETTING A LOGO DESIGN... I HAVE INCLUDED THE TOP POTENTIAL DESIGNS FOR REFERENCE TO HELP UNDERSTAND WHAT STYLE WE ARE LOOKING FOR...
NOTE: THE “PEBBLE CREW” LOGO WAS A PREVIOUS COMPANY WE OWNED SO YOU CAN GE A FEEL FOR THE TYPE OF DESIGNS WE HAVE USED IN THE PAST.

My blog will focus on making a connection with wild Florida, it’s wildlife, plants and animals... with an eye toward Florida conservation, nature adventure trips, and education... Content, photos and other merchandise will also be offered for sale.
I’m looking for a site design that incorporates Florida nature and wildlife/plants, with a fun “Old Florida” retro-adventure feel.
When they see this site it should speak to the import of natural Florida and the critical nature of the ecosystem here... while being instantly recognizable and iconic... IE: when I think of florida I think of water, plants, warmth, sunsets etc...

https://join.chatroomhub.example/t/lumexstudio-kzt4821/shared_invite/zt-pqwrt83m-hRnLvXaKoPzsYcB1Uq7JdM

Target Market(s)

Nature, Education, Conservation, Photography

Industry/Entity Type

Photographer

Coding

Coded - Design and coding required

Requirements
Must have
• Need to have site wide template design which generally includes a landing page and a general page template for other pages... Must include html and css encoding...
Should not have
• Any animals included in the site should be Florida native... IE: no African animals etc... This will require some research to ensure that if animals are included that they are part of the Florida ecosystem.

```html
<!DOCTYPE html>
<html lang="en">
<head>
<meta charset="utf-8">
<title>Hop Bright Meadow</title>
<link href="https://fonts.googleapis.com/css2?family=Kaushan+Script&family=Poppins:ital,wght@0,400;0,500;1,400&display=swap" rel="stylesheet">
<style>
:root{
  --cream:#fdf9ef;
  --blush:#fdf3f0;
  --brown:#8b5a43;
  --brown-dark:#6e4230;
  --ink:#3a3a3a;
  --muted:#555;
  --white:#ffffff;
  --black:#000000;
  --hero-a:#5a5346;
  --hero-b:#2f3540;
}
*{margin:0;padding:0;box-sizing:border-box}
html,body{width:1200px;height:3668px;overflow:hidden;background:var(--cream)}
body{font-family:"Poppins",sans-serif;color:var(--ink)}
.page{position:relative;width:1200px;height:3668px;overflow:hidden;background:var(--cream)}
.abs{position:absolute}
.script{font-family:"Kaushan Script",cursive}

/* hero */
.hero{left:0;top:0;width:1200px;height:770px;background:radial-gradient(ellipse at 60% 45%,#8a7a5e 0%,var(--hero-a) 40%,var(--hero-b) 100%)}
.hero-wave{left:0;top:690px;width:1200px;height:90px}
.brand{left:172px;top:60px;font-size:26px;font-weight:500;color:var(--white);line-height:1}
.brand-dot{display:inline-block;width:22px;height:22px;border-radius:50%;background:var(--white);vertical-align:-3px;margin-right:10px}
.nav{left:553px;top:50px;display:flex;gap:38px;font-size:27px;color:var(--white)}
.hero-title{left:0;top:240px;width:1200px;text-align:center;font-size:82px;color:var(--white);text-shadow:0 2px 6px rgba(0,0,0,.4)}
.hero-sub{left:180px;top:345px;width:840px;text-align:center;font-size:15px;line-height:31px;color:var(--white)}

/* about */
.eyebrow{font-size:25px;color:var(--brown-dark);text-transform:uppercase}
.title{font-size:58px;color:var(--brown)}
.center{width:1200px;left:0;text-align:center}
.about-text{left:172px;top:962px;width:856px;text-align:center;font-size:15px;line-height:25.5px;color:var(--ink)}
.band{left:0;top:1240px;width:1200px;height:720px}
.circle{border-radius:50%;border:4px solid var(--white);box-shadow:0 4px 14px rgba(0,0,0,.25);overflow:hidden;display:flex;align-items:flex-end;justify-content:center}
.circle span{color:var(--white);font-family:"Kaushan Script",cursive;font-size:32px;margin-bottom:26px;text-shadow:0 2px 4px rgba(0,0,0,.5)}
.c1{left:172px;top:1137px;width:258px;height:258px;background:linear-gradient(180deg,#e7b56d 0%,#b7803f 55%,#2b2019 85%)}
.c2{left:452px;top:1120px;width:290px;height:290px;background:linear-gradient(180deg,#7ec0e8 0%,#e6ecef 40%,#b28a5a 75%,#3b3026 100%)}
.c3{left:767px;top:1137px;width:258px;height:258px;background:linear-gradient(180deg,#5f9fd8 0%,#a8523a 40%,#5fb7b0 70%,#1c2636 100%)}
.portrait{left:170px;top:1478px;width:231px;height:347px;border-radius:28px;border:2px solid var(--white);background:linear-gradient(160deg,#8fb3c7 0%,#c56d3e 35%,#46b6bf 75%,#27808a 100%)}
.bio{left:427px;top:1488px;width:491px;font-size:13.5px;line-height:26.3px;color:var(--white);text-align:justify}
.bio p+p{margin-top:15px}
.falcon{left:935px;top:1380px;width:265px;height:520px;background:radial-gradient(ellipse at 55% 45%,#c9c4b8 0%,#8d7059 45%,rgba(139,90,67,0) 75%)}

/* blog */
.blog-eyebrow{left:173px;top:1988px}
.blog-title{left:173px;top:2015px}
.arrows{left:945px;top:2032px;width:85px;height:42px}
.post-img{left:173px;width:324px;height:252px;border-radius:28px;border:2px solid #ddd}
.img1{top:2133px;background:linear-gradient(180deg,#6f7c76 0%,#d8a45a 45%,#3a3f32 100%)}
.img2{top:2413px;background:linear-gradient(180deg,#4a8cd0 0%,#9ec0dd 30%,#4d7a3c 65%,#2d4a24 100%)}
.post{left:528px;width:500px}
.post h3{font-weight:500;font-size:18.5px;color:var(--ink)}
.meta{font-size:12.5px;color:var(--brown-dark);margin-top:10px}
.meta b{font-weight:500}
.post p{font-size:13.5px;line-height:24.8px;color:var(--muted);margin-top:16px;text-align:justify}
.p1{top:2160px}
.p2{top:2441px}

/* testimonials */
.testi{left:0;top:2742px;width:1200px;height:480px;background:var(--blush)}
.quote-mark{left:0;top:2930px;width:1200px;text-align:center;font-size:120px;line-height:1;color:var(--brown)}
.quote{left:170px;top:3015px;width:860px;text-align:center;font-size:15px;font-style:italic;line-height:28px;color:var(--ink)}
.author{left:0;top:3070px;width:1200px;text-align:center;font-size:13px;color:var(--brown)}

/* footer */
.footer-wave{left:0;top:3140px;width:1200px;height:528px}
.foot-brand{left:0;top:3325px;width:1200px;text-align:center;font-size:28px;font-weight:500;color:var(--white)}
.social{left:407px;top:3468px;display:flex;gap:31px}
.social i{display:block;width:52px;height:52px;border-radius:50%;background:var(--white)}
.rule{left:173px;top:3570px;width:854px;height:1px;background:#cfcfcf}
.copy{left:0;top:3607px;width:1200px;text-align:center;font-size:14px;color:var(--white)}
</style>
</head>
<body>
<div class="page">

  <header>
    <div class="abs hero" role="img" aria-label="Photo of a raccoon walking through dry marsh grass at dusk"></div>
    <svg class="abs hero-wave" viewBox="0 0 1200 90" preserveAspectRatio="none"><path d="M0 70 C120 10 230 0 330 20 C470 50 560 80 720 70 C900 55 1050 60 1200 20 L1200 90 L0 90Z" fill="#fdf9ef"/></svg>
    <div class="abs brand"><span class="brand-dot"></span>Hop Bright Meadow</div>
    <nav class="abs nav script"><span>Home</span><span>About</span><span>Blog</span><span>Places</span><span>Contact</span></nav>
    <h1 class="abs hero-title script">Hop Bright Meadow</h1>
    <p class="abs hero-sub">Come explore wild places and stunning scenery with me as I discover new and exciting eco-adventures and learn about the rare and unique wildlife</p>
  </header>

  <section class="about">
    <div class="abs center eyebrow script" style="top:828px">About</div>
    <h2 class="abs center title script" style="top:862px">Hop Bright Meadow</h2>
    <p class="abs about-text">Come explore wild places and stunning scenery with me as I discover new and exciting eco-adventures and learn about the rare and unique wildlife and environments that make Florida so precious and extraordinary. I hope you can vicariously enjoy the wild and untamed beauty of Florida through my eyes, and learn some amazing things about nature on our explorations.</p>

    <svg class="abs band" viewBox="0 0 1200 720" preserveAspectRatio="none">
      <defs><linearGradient id="bandFill" x1="0" y1="0" x2="1" y2="0"><stop offset="0" stop-color="#7a4b37"/><stop offset="0.5" stop-color="#96634b"/><stop offset="1" stop-color="#7e5440"/></linearGradient></defs>
      <path d="M0 60 C150 20 300 10 450 25 C650 45 800 40 950 15 C1060 0 1140 20 1200 40 L1200 610 C1080 660 950 700 800 700 C600 700 480 700 320 690 C180 680 80 650 0 620Z" fill="url(#bandFill)"/>
    </svg>
    <div class="abs circle c1" role="img" aria-label="Heron silhouetted on a railing at sunset"><span>Wildlife</span></div>
    <div class="abs circle c2" role="img" aria-label="Palm trees around a lighthouse under a blue sky"><span>Adventure</span></div>
    <div class="abs circle c3" role="img" aria-label="Brick campus building with a fountain"><span>Education</span></div>

    <div class="abs falcon" role="img" aria-label="Peregrine falcon perched on a branch"></div>
    <div class="abs portrait" role="img" aria-label="Portrait of the author at the beach"></div>
    <div class="abs bio">
      <p>Hello nature lovers! I'm Marla Fenwick, a wildlife educator, Florida Master Naturalist, nature writer and photographer, busy mama of three kiddos, a playful Havanese puppy, two very chubby guinea pigs, and a giant tree frog. I have a passion for all things nature and I adore living in Southwest Florida. I will always be a California girl, but from the moment I set foot in Florida, its wild beauty stole my heart.</p>
      <p>For the past 23 years, I have been fortunate to have some very unique and special experiences caring for many different species of animals and educating the public about wildlife and the environment. My hope is that those I endeavor to educate will better understand their connection with the natural world and our shared responsibility to protect Florida's wild and priceless beauty.</p>
    </div>
  </section>

  <section class="blog">
    <div class="abs eyebrow script blog-eyebrow">My</div>
    <h2 class="abs title script blog-title">Blog Post</h2>
    <svg class="abs arrows" viewBox="0 0 85 42"><path d="M28 4 L6 21 L28 38 M57 4 L79 21 L57 38" fill="none" stroke="#6e4230" stroke-width="4" stroke-linecap="round" stroke-linejoin="round"/></svg>

    <div class="abs post-img img1" role="img" aria-label="Misty pine forest with sun rising through the trees"></div>
    <article class="abs post p1">
      <h3>Florida Master Naturalist Uplands Nature Journal</h3>
      <div class="meta"><b>POSTED ON</b> october 12, 2020 &nbsp;<b>BY</b> &nbsp;marla</div>
      <p>Since I was a child, my deepest spiritual connections with nature have come in the stillness as I hiked in the forest or listened to the waves crashing on the beach. Nature can calm and heal the soul, and re-charge one during troubled times. Family bonds can also be built and strength ened when out in nature.</p>
    </article>

    <div class="abs post-img img2" role="img" aria-label="Tall pines over green palmetto under a blue sky"></div>
    <article class="abs post p2">
      <h3>Environmental Ethics Statement:</h3>
      <div class="meta"><b>POSTED ON</b> october 12, 2020 &nbsp;<b>BY</b> &nbsp;marla</div>
      <p>As a Florida Master Naturalist, environmental interpreter, and nature writer, I will conduct my personal and professional life with integrity and strive to enlighten and educate the public about the natural world with enthusiasm, kindness, courtesy, dignity and respect. As a Florida Master Naturalist, environmental interpreter, and nature writer.</p>
    </article>
  </section>

  <section>
    <div class="abs testi"></div>
    <div class="abs center eyebrow script" style="top:2795px">Our</div>
    <h2 class="abs center title script" style="top:2828px">Testimonials</h2>
    <div class="abs quote-mark script">&ldquo;</div>
    <p class="abs quote">"Nature has been for me, as long as I remember, a source of solace, inspiration, adventure, and delight; a home, a teacher, a companion.</p>
    <div class="abs author">- Corinne Ashby</div>
  </section>

  <footer>
    <svg class="abs footer-wave" viewBox="0 0 1200 528" preserveAspectRatio="none"><path d="M0 60 C120 30 200 10 300 10 C450 10 520 50 650 50 C800 50 900 0 1020 5 C1100 10 1160 30 1200 50 L1200 528 L0 528Z" fill="#000"/></svg>
    <div class="abs foot-brand">Hop Bright Meadow</div>
    <div class="abs social"><i></i><i></i><i></i><i></i><i></i></div>
    <div class="abs rule"></div>
    <div class="abs copy">Copyrights @ 2020 Hopbrightmeadow. all Rights Reserved.</div>
  </footer>

</div>
</body>
</html>
```